Website mockup using figma or other design software for Plumbing Company

We are looking for a talented UI/UX designer to create a high-converting, modern, and professional website design for a local plumbing company. The goal is to move away from the "dated" look of traditional trades and provide a seamless, trustworthy experience for homeowners and commercial clients.
The Challenge
Create a Homepage and a Service Page design that balances professional expertise with an urgent "call-to-action" (CTA) focus. We need a design that looks great on desktop but is built with a mobile-first mindset, as most customers find plumbers via their phones during emergencies.
This company will focus more on B2B, and corporate contracts, but should still be friendly to the public.
Here are some examples of what we are looking for
https://velotrin-works.com/construction/plumbing-construction/
https://velotrin-works.com/
The company is called "KT Plumbing."
Please see the logo below.

```html
<!DOCTYPE html>
<html lang="en">
<head>
<meta charset="utf-8">
<title>Velotrin – Plumbing Division</title>
<link href="https://fonts.googleapis.com/css2?family=Orbitron:wght@700;800&family=Roboto:ital,wght@0,400;0,500;0,700;0,900;1,400&display=swap" rel="stylesheet">
<style>
:root{
  --ink:#2b2b2b;
  --dark:#262626;
  --footer:#2a2a2a;
  --panel:#f3f3f3;
  --grey-shape:#e4e4e4;
  --white:#ffffff;
  --text:#555555;
  --muted:#8a8a8a;
  --line:#cfcfcf;
}
*{box-sizing:border-box;margin:0;padding:0}
html,body{width:1200px;height:4135px;overflow:hidden}
body{position:relative;background:var(--white);font-family:"Roboto",Arial,sans-serif;color:var(--ink)}
.abs{position:absolute}
.display{font-family:"Orbitron","Roboto",sans-serif;font-weight:800;letter-spacing:1px}

/* header + hero */
.hero{left:0;top:0;width:1200px;height:786px;
  background:linear-gradient(180deg,#1d1d22 0%,#3a3e48 22%,#4a5668 40%,#2c5da8 62%,#1f4f9c 78%,#4f4a44 100%)}
.brand{display:flex;align-items:center;gap:12px;color:var(--white);font-weight:900;font-size:34px;letter-spacing:1px}
.brand .mark{width:40px;height:40px;background:var(--white)}
.nav{left:482px;top:66px;display:flex;gap:26px;font-size:13px;font-weight:700;color:var(--white);text-transform:uppercase}
.btn{display:flex;align-items:center;justify-content:center;height:50px;font-weight:700;font-size:16px;text-transform:uppercase;text-decoration:none;white-space:nowrap;
  clip-path:polygon(8px 0,100% 0,calc(100% - 12px) 100%,0 100%)}
.btn-light{background:var(--white);color:var(--ink)}
.btn-dark{background:var(--dark);color:var(--white)}
.slashes{width:36px;height:50px}
.hero-title{left:142px;top:244px;font-size:44px;line-height:60px;color:var(--white)}
.hero-sub{left:143px;top:444px;font-size:23px;line-height:34px;font-weight:500;color:var(--white)}

/* about */
.about-title{left:145px;top:895px;font-size:42px}
.about-copy{left:145px;top:972px;width:463px;font-size:15px;line-height:28px;color:var(--text);text-align:justify}

/* section headings */
.section-title{left:0;width:1200px;text-align:center;font-size:42px}
.cap-sub{left:0;width:1200px;text-align:center;top:1574px;font-size:17px;color:var(--ink)}
.cap-label{width:300px;text-align:center;font-size:17px;font-weight:500}
.arrow-circle{fill:none;stroke:#555;stroke-width:1.6}

/* reviews */
.review{background:var(--white);height:180px;padding:26px 20px 0;text-align:center;overflow:hidden}
.review.active{border:1px solid #c8c8c8;box-shadow:0 2px 6px rgba(0,0,0,.08)}
.quote{font-family:Georgia,serif;font-weight:700;font-size:52px;line-height:30px;color:var(--ink)}
.review p{margin-top:10px;font-size:11px;line-height:22px;font-style:italic;color:var(--muted)}
.author{display:flex;align-items:center;gap:10px}
.avatar{width:42px;height:42px;border-radius:50%;background:linear-gradient(135deg,#c9b8a6,#8b7867)}
.author b{display:block;font-size:16px;font-weight:500}
.author small{font-size:10px;color:var(--text)}

/* footer */
.footer{left:0;top:3567px;width:1200px;height:568px;background:var(--footer)}
.f-head{font-size:17px;font-weight:700;color:var(--white)}
.radio{display:flex;gap:22px;font-size:12px;color:#ddd}
.radio span{display:flex;align-items:center;gap:7px}
.radio i{width:12px;height:12px;border:1px solid #ddd;border-radius:50%}
.field{border:1px solid #8a8a8a;height:30px;padding:5px 10px;font-size:14px;color:#eee}
.contact-line{font-size:14px;line-height:21px;color:#eee}
.icon-ring{width:34px;height:34px;border:1.5px solid #eee;border-radius:50%;display:flex;align-items:center;justify-content:center}
.social{display:flex;gap:8px}
.social i{width:27px;height:27px;border:1.5px solid #eee;border-radius:50%}
.legal{left:0;width:1200px;top:4070px;text-align:center;font-size:14px;color:#eee}
</style>
</head>
<body>

<!-- Hero -->
<div class="abs hero" role="img" aria-label="Photo of long rows of blue pipeline on supports at dusk"></div>
<div class="abs brand" style="left:148px;top:50px"><span class="mark"></span>VELOTRIN</div>
<nav class="abs nav"><span>Home</span><span>About</span><span>Services</span><span>Contact Us</span></nav>
<a class="abs btn btn-light" style="left:864px;top:50px;width:160px;height:46px;font-size:14px">Request Service</a>
<svg class="abs slashes" style="left:1022px;top:48px" viewBox="0 0 36 50"><g stroke="#fff" stroke-width="4"><line x1="10" y1="0" x2="2" y2="50"/><line x1="20" y1="0" x2="12" y2="50"/><line x1="30" y1="0" x2="22" y2="50"/></g></svg>

<h1 class="abs display hero-title">RELIABLE PLUMBING<br>SOLUTIONS FOR HOMES<br>&amp; BUSINESSES</h1>
<p class="abs hero-sub">Emergency repairs, commercial installations,<br>and long-term service contracts.</p>
<a class="abs btn btn-light" style="left:145px;top:552px;width:190px;height:52px;font-size:17px">Request Service</a>
<svg class="abs slashes" style="left:334px;top:552px;height:52px" viewBox="0 0 36 50"><g stroke="#fff" stroke-width="4"><line x1="10" y1="0" x2="2" y2="50"/><line x1="20" y1="0" x2="12" y2="50"/><line x1="30" y1="0" x2="22" y2="50"/></g></svg>
<svg class="abs" style="left:586px;top:676px" width="28" height="70" viewBox="0 0 28 70"><rect x="4" y="1" width="20" height="38" rx="10" fill="none" stroke="#fff" stroke-width="2"/><line x1="14" y1="9" x2="14" y2="17" stroke="#fff" stroke-width="2"/><polyline points="4,46 14,56 24,46" fill="none" stroke="#fff" stroke-width="2"/><polyline points="4,56 14,66 24,56" fill="none" stroke="#fff" stroke-width="2"/></svg>

<!-- About -->
<svg class="abs" style="left:0;top:786px" width="1200" height="610" viewBox="0 0 1200 610">
  <polygon points="1000,8 1200,8 1200,330" fill="var(--grey-shape)"/>
  <polygon points="590,608 700,608 660,420" fill="var(--grey-shape)"/>
  <polygon points="610,8 995,8 1200,608 705,608" fill="#8c8e8a" role="img" aria-label="Photo of stainless steel water treatment tanks and blue valves in a plant room"/>
</svg>
<h2 class="abs display about-title">ABOUT US</h2>
<p class="abs about-copy">Velotrin's Plumbing Division offers clients design, fabrication, and installation for commercial and industrial plumbing systems. As part of a MEP package or stand-alone, our team self-performs process piping, domestic water, medical gas, natural gas, waste/vent, and storm drainage systems.<br>Nemo enim ipsam voluptatem quia voluptas sit aspernatur aut odit aut fugit, sed quia consequuntur magni dolores eos qui ratione voluptatem sequi nesque porro quisquam</p>
<a class="abs btn btn-dark" style="left:145px;top:1228px;width:158px">Read More</a>
<svg class="abs slashes" style="left:298px;top:1228px" viewBox="0 0 36 50"><g stroke="var(--dark)" stroke-width="4"><line x1="10" y1="0" x2="2" y2="50"/><line x1="20" y1="0" x2="12" y2="50"/><line x1="30" y1="0" x2="22" y2="50"/></g></svg>

<!-- Capabilities -->
<svg class="abs" style="left:0;top:1400px" width="1200" height="750" viewBox="0 0 1200 750"><polygon points="32,0 1198,0 1160,748 0,748 0,130" fill="var(--panel)"/></svg>
<h2 class="abs display section-title" style="top:1500px">OUR CAPABILITES</h2>
<p class="abs cap-sub">Velotrin can design, fabricate, and install any plumbing project need for our customers including:</p>
<svg class="abs" style="left:0;top:1650px" width="1200" height="250" viewBox="0 0 1200 250">
  <polygon points="180,2 445,2 410,242 145,242" fill="#6f93b8" role="img" aria-label="Photo of insulated piping in a glass-roofed plant"/>
  <polygon points="490,2 748,2 713,242 455,242" fill="#3f64b0" stroke="#ddd" stroke-width="4" role="img" aria-label="Photo of blue laboratory gas regulators and gauges"/>
  <polygon points="810,2 1055,2 1020,242 775,242" fill="#5f7686" role="img" aria-label="Photo of deionized water treatment equipment"/>
  <circle cx="600" cy="125" r="40" fill="#fff"/>
  <circle cx="600" cy="116" r="9" fill="none" stroke="#444" stroke-width="2"/>
  <rect x="584" y="128" width="32" height="12" fill="none" stroke="#444" stroke-width="2"/>
  <circle class="arrow-circle" cx="113" cy="105" r="17"/><polyline points="117,96 109,105 117,114" fill="none" stroke="#555" stroke-width="1.6"/>
  <circle class="arrow-circle" cx="1087" cy="105" r="17"/><polyline points="1083,96 1091,105 1083,114" fill="none" stroke="#555" stroke-width="1.6"/>
</svg>
<div class="abs cap-label" style="left:145px;top:1914px">Medical Gas Systems</div>
<div class="abs cap-label" style="left:450px;top:1914px">Laboratory Air &amp; Gas Systems</div>
<div class="abs cap-label" style="left:755px;top:1914px">Deionized Water Systems</div>
<a class="abs btn btn-dark" style="left:505px;top:1986px;width:157px;height:52px">View More</a>
<svg class="abs slashes" style="left:657px;top:1987px" viewBox="0 0 36 50"><g stroke="var(--dark)" stroke-width="4"><line x1="10" y1="0" x2="2" y2="50"/><line x1="20" y1="0" x2="12" y2="50"/><line x1="30" y1="0" x2="22" y2="50"/></g></svg>

<!-- Gallery -->
<h2 class="abs display section-title" style="top:2255px">PROJECT GALLERY</h2>
<svg class="abs" style="left:0;top:2348px" width="1200" height="500" viewBox="0 0 1200 500">
  <polygon points="190,2 400,2 375,244 160,244" fill="#cfcfcc" role="img" aria-label="Photo of a hand fitting a white basin"/>
  <polygon points="410,2 622,2 597,244 385,244" fill="#9d8f84" role="img" aria-label="Photo of copper pipework under a sink"/>
  <polygon points="632,2 845,2 820,244 607,244" fill="#c8703f" role="img" aria-label="Photo of a worker brazing copper pipe"/>
  <polygon points="855,2 1068,2 1043,244 830,244" fill="#6c8a45" role="img" aria-label="Photo of a worker in hard hat fitting pipe"/>
  <polygon points="160,254 370,254 345,496 132,496" fill="#8fa4a8" role="img" aria-label="Photo of water filtration housings"/>
  <polygon points="380,254 592,254 567,496 355,496" fill="#9ea3a6" role="img" aria-label="Photo of a pressure gauge on steel pipe"/>
  <polygon points="602,254 815,254 790,496 577,496" fill="#7d6f62" role="img" aria-label="Photo of a worker soldering with a torch"/>
  <polygon points="825,254 1040,254 1015,496 800,496" fill="#c9cdcf" role="img" aria-label="Photo of gas regulators on a white wall"/>
  <circle cx="503" cy="123" r="21" fill="none" stroke="#fff" stroke-width="2"/>
  <path d="M503 114v18M494 123h18" stroke="#fff" stroke-width="2.5"/>
</svg>
<a class="abs btn btn-dark" style="left:505px;top:2882px;width:157px;height:52px">View More</a>
<svg class="abs slashes" style="left:657px;top:2883px" viewBox="0 0 36 50"><g stroke="var(--dark)" stroke-width="4"><line x1="10" y1="0" x2="2" y2="50"/><line x1="20" y1="0" x2="12" y2="50"/><line x1="30" y1="0" x2="22" y2="50"/></g></svg>

<!-- Reviews -->
<svg class="abs" style="left:0;top:3012px" width="1200" height="556" viewBox="0 0 1200 556"><polygon points="82,0 1200,0 1200,556 0,556 0,380" fill="var(--panel)"/>
  <circle class="arrow-circle" cx="97" cy="313" r="17"/><polyline points="101,304 93,313 101,322" fill="none" stroke="#555" stroke-width="1.6"/>
  <circle class="arrow-circle" cx="1103" cy="313" r="17"/><polyline points="1099,304 1107,313 1099,322" fill="none" stroke="#555" stroke-width="1.6"/>
</svg>
<h2 class="abs display section-title" style="top:3118px">CUSTOMER REVIEWS</h2>
<div class="abs review" style="left:135px;top:3228px;width:300px"><div class="quote">“</div><p>Lorem ipsum dolor sit amet, consectetur adipiscing elit, sed do eiusmod tempor incididunt ut labore et dolore magna aliqu enim ad minim veniam,ullamco laboris nisi ut aliquip ex ea commodoullamco laboris nisi</p></div>
<div class="abs review active" style="left:450px;top:3228px;width:305px"><div class="quote">“</div><p>Lorem ipsum dolor sit amet, consectetur adipiscing elit, sed do eiusmod tempor incididunt ut labore et dolore magna aliqu enim ad minim veniam,ullamco laboris nisi ut aliquip ex ea commodoullamco laboris nisi</p></div>
<div class="abs review" style="left:772px;top:3228px;width:294px"><div class="quote">“</div><p>Lorem ipsum dolor sit amet, consectetur adipiscing elit, sed do eiusmod tempor incididunt ut labore et dolore magna aliqu enim ad minim veniam,ullamco laboris nisi ut aliquip ex ea commodoullamco laboris nisi</p></div>
<div class="abs author" style="left:210px;top:3433px"><span class="avatar" role="img" aria-label="Customer portrait"></span><div><b>Owen Tallis</b><small>orem ipsu</small></div></div>
<div class="abs author" style="left:523px;top:3433px"><span class="avatar" role="img" aria-label="Customer portrait"></span><div><b>Nora Vesk</b><small>orem ipsu</small></div></div>
<div class="abs author" style="left:847px;top:3433px"><span class="avatar" role="img" aria-label="Customer portrait"></span><div><b>Dario Menotti</b><small>orem ipsu</small></div></div>

<!-- Footer -->
<footer class="abs footer"></footer>
<div class="abs brand" style="left:470px;top:3625px;font-size:36px"><span class="mark" style="width:44px;height:44px"></span>VELOTRIN</div>
<div class="abs f-head" style="left:172px;top:3736px">Get In Touch:</div>
<div class="abs radio" style="left:357px;top:3740px"><span><i></i>General</span><span><i></i>Estimating</span><span><i></i>Service</span></div>
<div class="abs field" style="left:173px;top:3776px;width:267px">Name :</div>
<div class="abs field" style="left:450px;top:3776px;width:265px">Phone :</div>
<div class="abs field" style="left:173px;top:3816px;width:542px">Email :</div>
<div class="abs field" style="left:173px;top:3856px;width:542px;height:68px">Message :</div>
<div class="abs" style="left:631px;top:3942px;width:84px;height:28px;background:#fff;color:var(--ink);font-size:12px;font-weight:500;display:flex;align-items:center;justify-content:center;clip-path:polygon(6px 0,100% 0,calc(100% - 6px) 100%,0 100%)">SUBMIT</div>

<div class="abs f-head" style="left:786px;top:3736px">Contact Information</div>
<div class="abs icon-ring" style="left:786px;top:3778px"><svg width="14" height="18" viewBox="0 0 14 18"><path d="M7 1a6 6 0 0 0-6 6c0 4 6 10 6 10s6-6 6-10a6 6 0 0 0-6-6z" fill="#fff"/><circle cx="7" cy="7" r="2.2" fill="var(--footer)"/></svg></div>
<div class="abs contact-line" style="left:838px;top:3774px">4210 Harlow Bend Road<br>Fairmont, CA 95710<br>88 Quillon Drive<br>Renwick, NV 89120</div>
<div class="abs icon-ring" style="left:786px;top:3883px"><svg width="16" height="16" viewBox="0 0 16 16"><path d="M3 1l3 3-2 2c1 2 3 4 5 5l2-2 3 3-2 3C7 15 1 9 1 3z" fill="none" stroke="#fff" stroke-width="1.4"/></svg></div>
<div class="abs contact-line" style="left:838px;top:3882px">General Inquiries: 555-214-7730<br>Service Department: 555-214-7741</div>
<div class="abs social" style="left:788px;top:3935px"><i></i><i></i><i></i><i></i><i></i></div>
<div class="abs" style="left:135px;top:4026px;width:930px;height:1px;background:#555"></div>
<div class="abs legal">Copyrights © 2026 Companyname. All Rights Reserved. &nbsp;| &nbsp;Privacy Policy &nbsp;| &nbsp;Terms of Use</div>

</body>
</html>
```